Business Card Design

New business card design

Target Market(s)

Residential & Commercial Property Managers

Industry/Entity Type

Plumbing Services

Contact Information for Business Card

Name - Rowan Keddle, title - Director, Phone Number - 0431 286 517, email - rowan@tbk-plumbing.com.au, Company ABN - 73 215 904 386,

Font styles to use
Sans Serif

Colors
0054AA
0677BA
7BADD7
CADEEF
E8F1F8

```html
<!DOCTYPE html>
<html lang="en">
<head>
<meta charset="utf-8">
<title>TBK Plumbing Services – Business Card</title>
<link rel="stylesheet" href="https://fonts.googleapis.com/css2?family=Lato:wght@300;400;700;900&display=swap">
<style>
  :root {
    --stage: #26292d;
    --card: #1e232a;
    --card-edge: #161a1f;
    --accent: #00aeef;
    --ink-light: #e9eef2;
    --ink-muted: #8a939c;
    --divider: #3a424b;
  }
  * { box-sizing: border-box; margin: 0; padding: 0; }
  html, body {
    width: 1200px; height: 952px; overflow: hidden;
    background: var(--stage);
    font-family: "Lato", Arial, sans-serif;
  }
  .stage {
    width: 1200px; height: 952px;
    display: flex; align-items: center; justify-content: center; gap: 40px;
  }
  .card {
    position: relative;
    width: 540px; height: 330px;
    background: var(--card);
    border-radius: 3px;
    overflow: hidden;
    box-shadow: 0 3px 0 var(--card-edge), 0 6px 0 #14181c, 0 20px 40px rgba(0,0,0,.45);
  }

  /* Front */
  .front-band {
    position: absolute; left: 0; top: 0;
    width: 540px; height: 330px;
  }
  .front-wordmark {
    position: absolute; left: 64px; top: 88px;
    color: var(--card);
  }
  .wordmark-name {
    font-weight: 700; font-size: 72px; letter-spacing: 4px; line-height: 1;
    text-transform: lowercase;
  }
  .wordmark-tag {
    margin-top: 8px;
    font-weight: 400; font-size: 13px; letter-spacing: 9px;
    text-transform: lowercase;
  }

  /* Back */
  .edge-bar {
    position: absolute; background: var(--accent);
  }
  .edge-bar.top { left: 0; top: 0; width: 10px; height: 96px; }
  .edge-bar.bottom { right: 0; bottom: 0; width: 10px; height: 110px; }
  .back-wordmark {
    position: absolute; left: 52px; top: 92px; width: 200px;
    color: var(--ink-light);
  }
  .back-wordmark .wordmark-name { font-size: 54px; letter-spacing: 3px; }
  .back-wordmark .wordmark-tag { font-size: 10px; letter-spacing: 7px; color: var(--ink-muted); }
  .divider {
    position: absolute; left: 266px; top: 70px;
    width: 1px; height: 150px; background: var(--divider);
  }
  .contact {
    position: absolute; left: 292px; top: 88px;
    color: var(--ink-light);
  }
  .contact-name {
    color: var(--accent); font-weight: 900; font-size: 21px;
    letter-spacing: 1px; text-transform: uppercase;
  }
  .contact-title { font-size: 15px; margin-top: 2px; margin-bottom: 16px; }
  .contact-line {
    display: flex; align-items: center; gap: 8px;
    font-size: 14px; margin-bottom: 7px;
  }
  .contact-line svg { width: 13px; height: 13px; fill: var(--accent); flex: none; }
  .abn {
    position: absolute; left: 52px; bottom: 46px;
    font-size: 14px; color: var(--ink-light); letter-spacing: .5px;
  }
  .abn-label { color: var(--accent); }
</style>
</head>
<body>
<main class="stage">

  <section class="card card-front" aria-label="Card front">
    <svg class="front-band" viewBox="0 0 540 330" aria-hidden="true">
      <path d="M0 60 H360 C420 60 440 120 470 180 C490 220 510 240 540 250 V330 H540 C500 300 440 270 400 270 H0 Z" fill="var(--accent)"/>
    </svg>
    <div class="front-wordmark">
      <div class="wordmark-name">tbk</div>
      <div class="wordmark-tag">plumbing services</div>
    </div>
  </section>

  <section class="card card-back" aria-label="Card back">
    <span class="edge-bar top"></span>
    <span class="edge-bar bottom"></span>

    <div class="back-wordmark">
      <div class="wordmark-name">tbk</div>
      <div class="wordmark-tag">plumbing services</div>
    </div>

    <span class="divider"></span>

    <div class="contact">
      <div class="contact-name">Rowan Keddle</div>
      <div class="contact-title">Director</div>
      <div class="contact-line">
        <svg viewBox="0 0 24 24" aria-hidden="true"><path d="M6.6 10.8a15.1 15.1 0 0 0 6.6 6.6l2.2-2.2a1 1 0 0 1 1-.25 11.4 11.4 0 0 0 3.6.57 1 1 0 0 1 1 1V20a1 1 0 0 1-1 1A17 17 0 0 1 3 4a1 1 0 0 1 1-1h3.5a1 1 0 0 1 1 1c0 1.25.2 2.45.57 3.57a1 1 0 0 1-.25 1z"/></svg>
        <span>0431 286 517</span>
      </div>
      <div class="contact-line">
        <svg viewBox="0 0 24 24" aria-hidden="true"><path d="M2 5h20v14H2z M2 5l10 8 10-8" fill="none" stroke="var(--accent)" stroke-width="2.4"/></svg>
        <span>rowan@tbk-plumbing.com.au</span>
      </div>
    </div>

    <div class="abn"><span class="abn-label">ABN -</span> 73 215 904 386</div>
  </section>

</main>
</body>
</html>
```